I have a business that exists already (Linden Conservatory of Music) that we offer music lessons to all instruments. I recently opened a smaller version called CHORDS by Linden that will only teach piano lessons. What I'm looking for now is a 3 page Website on word press. After I choose the design I like I want to be able to take over the website and bring it to our hosting company. We want full control of it and our team will take over. The reason I'm doing this is to have other visions and ideas from others. The first page will be about the company and our message/vision. Second page about the piano lessons. The third will be about franchising this concept "Chords by Linden" Attached are 3 Logos . Please refer to our existing website www.lindenmusicconservatory.example to look at our piano page and franchising page. Please feel free to message me if you need more info. Thanks
Please note I do not want the new website (Chords by Linden) To look like the other Website (Linden Conservatory of Music) Fresh new look. I do not want the colours red or using the Red logo. I only provided it so that you have an Idea of What the other business looks like and that you can take the piano content and franchise content off of it. Chords by Linden is smaller concept and only piano lessons.
Thanks
Only Piano lessons for all students
3 page

```html
<!DOCTYPE html>
<html lang="en">
<head>
<meta charset="utf-8">
<title>Chords by Linden</title>
<link rel="stylesheet" href="https://fonts.googleapis.com/css2?family=Cinzel:wght@400;600&family=Mulish:wght@400;600;700&family=Lora:ital@0;1&family=Great+Vibes&family=Open+Sans:wght@700&display=swap">
<style>
:root{
  --black:#000;
  --ink:#222;
  --text:#333;
  --muted:#888;
  --blue:#2b9ae8;
  --gold:#d9b95a;
  --gold-text:#e4c262;
  --tint:#f5f2f5;
  --white:#fff;
}
*{box-sizing:border-box;margin:0;padding:0}
html,body{width:1200px;height:3776px;overflow:hidden}
body{position:relative;background:var(--white);font-family:"Mulish",sans-serif;color:var(--text)}
section,header,footer{position:absolute;left:0;width:1200px}
.abs{position:absolute}
.btn{position:absolute;display:flex;align-items:center;justify-content:center;background:var(--blue);color:var(--white);font-family:"Cinzel",serif;font-size:16px;letter-spacing:1px}

/* header */
.site-header{top:0;height:80px;background:var(--black);z-index:2}
.brand{left:155px;top:18px;color:var(--white);font-family:"Cinzel",serif;font-size:26px;display:flex;align-items:center;gap:8px}
.brand-dot{width:10px;height:10px;background:var(--white);border-radius:50%}
.nav{left:485px;top:32px;display:flex;gap:0;font-family:"Cinzel",serif;font-size:13px;color:var(--white)}
.nav a{position:absolute;white-space:nowrap;color:inherit;text-decoration:none}
.nav .active{color:var(--gold-text)}
.nav-divider{left:971px;top:22px;width:1px;height:36px;background:#555}
.social{left:1000px;top:35px;display:flex;gap:23px}
.social span{width:11px;height:11px;border-radius:50%;background:var(--gold-text)}

/* hero */
.hero{top:0;height:632px;background:linear-gradient(90deg,#0a0807 0%,#1d1612 40%,#5a3a22 70%,#2a1a10 100%)}
.hero-welcome{left:150px;top:225px;font-family:"Great Vibes",cursive;font-size:72px;color:var(--gold-text)}
.hero-title{left:150px;top:318px;font-family:"Cinzel",serif;font-size:55px;color:var(--white);letter-spacing:1px}
.hero-btn{left:149px;top:410px;width:121px;height:36px;background:var(--gold);color:var(--ink);font-size:13px}

/* about */
.about{top:632px;height:572px}
.section-title{left:0;width:1200px;text-align:center;font-family:"Cinzel",serif}
.about-title{top:56px;font-size:30px;color:var(--ink)}
.about-title .accent{color:var(--blue);margin-right:10px}
.title-rule{left:540px;width:120px;height:2px;background:linear-gradient(90deg,var(--blue) 50%,var(--ink) 50%)}
.lead{left:0;width:1200px;text-align:center;font-size:14px;line-height:25px;color:var(--text)}
.about-lead{top:114px}
.about-photos{left:141px;top:186px;width:426px;height:318px}
.about-photos .frame{position:absolute;background:#e6e6e6}
.about-photos .photo{position:absolute}
.about-heading{left:592px;top:236px;font-family:"Lora",serif;font-style:italic;font-size:30px;color:var(--blue)}
.about-copy{left:592px;top:288px;width:470px;font-size:14px;line-height:25.6px}
.about-copy p+p{margin-top:4px}
.about-btn{left:592px;top:456px;width:155px;height:36px}

/* vision */
.vision{top:1204px;height:339px;background:linear-gradient(100deg,#1a1a1a 0%,#3e3e3e 45%,#2a2a2a 75%,#111 100%)}
.vision-title{top:60px;font-size:33px;color:var(--white)}
.vision-lead{top:129px;color:var(--white);line-height:25.6px}
.vision-btn{left:508px;top:224px;width:184px;height:34px}

/* programs */
.programs{top:1543px;height:571px}
.programs-title{left:141px;top:72px;padding-left:18px;border-left:6px solid var(--ink);font-family:"Lora",serif;font-size:18px;line-height:24px;color:var(--blue);text-transform:uppercase}
.programs-photo{left:141px;top:143px;width:345px;height:315px;border:7px solid var(--blue);background:linear-gradient(135deg,#f2f2f2,#cfc9c2 60%,#6f5b4a)}
.program-card{position:absolute;width:268px;height:91px;background:var(--white);box-shadow:0 2px 8px rgba(0,0,0,.12)}
.program-card p{position:absolute;left:12px;top:14px;right:12px;padding-left:12px;border-left:3px solid var(--blue);font-size:12.5px;line-height:19px;color:var(--text)}

/* franchise */
.franchise{top:2114px;height:245px;background:var(--tint)}
.franchise-title{top:55px;font-size:38px;color:var(--ink);letter-spacing:1px}
.franchise-sub{top:112px;font-family:"Lora",serif;font-size:16px;color:var(--ink)}
.franchise-btn{left:529px;top:149px;width:141px;height:34px}

/* quote */
.quote{top:2359px;height:401px}
.quote-accent{left:195px;top:70px;width:182px;height:182px;border-radius:50%;background:var(--blue)}
.quote-portrait{left:221px;top:106px;width:226px;height:226px;border-radius:50%;background:radial-gradient(circle at 50% 40%,#c9a48a,#8a9bb0 70%,#e9edf2);border:4px solid var(--white)}
.quote-mark{font-family:"Lora",serif;font-size:90px;line-height:1;color:#999}
.quote-text{left:548px;top:188px;width:520px;font-family:"Lora",serif;font-style:italic;font-size:22px;line-height:34px;color:var(--ink)}
.quote-author{left:548px;top:268px;font-family:"Lora",serif;font-weight:700;font-size:15px;color:var(--ink)}

/* contact */
.contact{top:2760px;height:668px;background:var(--tint)}
.contact-title{top:72px;font-size:36px;color:var(--ink)}
.contact-title .accent{color:var(--blue)}
.contact-lead{top:138px}
.contact-form{left:277px;top:218px;width:359px;height:362px;background:var(--white);box-shadow:0 4px 20px rgba(0,0,0,.12)}
.field{position:absolute;left:29px;width:295px;height:36px;background:var(--white);box-shadow:0 2px 6px rgba(0,0,0,.12);font-family:"Lora",serif;font-style:italic;font-size:13px;color:#999;padding:10px 14px}
.send-btn{left:32px;top:290px;width:295px;height:47px;font-family:"Open Sans",sans-serif;font-weight:700;font-size:18px;letter-spacing:0}
.contact-map{left:636px;top:207px;width:309px;height:391px;background:linear-gradient(135deg,#eee9df,#e3ddd0 50%,#f0ebe0)}

/* footer */
.site-footer{top:3428px;height:348px;background:var(--black)}
.info{position:absolute;width:260px;text-align:center;color:var(--white)}
.info-icon{width:70px;height:70px;border-radius:50%;background:var(--white);margin:0 auto 22px;display:flex;align-items:center;justify-content:center}
.info h3{font-family:"Cinzel",serif;font-weight:400;font-size:14px;letter-spacing:1px}
.info p{font-size:14px;line-height:21px}
.copyright{position:absolute;left:0;top:320px;width:1200px;height:28px;background:var(--blue)}
.copyright p{position:absolute;left:142px;top:6px;font-size:12px;color:var(--white)}
.copyright strong{font-weight:600}
.copyright .dots{position:absolute;left:965px;top:9px;display:flex;gap:16px}
.copyright .dots span{width:10px;height:10px;border-radius:50%;background:var(--white)}
</style>
</head>
<body>

<header class="site-header">
  <div class="abs brand"><span class="brand-dot"></span>CHORDS by Linden</div>
  <nav class="abs nav">
    <a class="active" style="left:0">HOME</a>
    <a style="left:88px">PIANO LESSONS</a>
    <a style="left:235px">FRANCHISING</a>
    <a style="left:370px">CONTACT US</a>
  </nav>
  <div class="abs nav-divider"></div>
  <div class="abs social"><span></span><span></span><span></span><span></span></div>
</header>

<section class="hero" role="img" aria-label="Photo of a pianist playing a grand piano in warm stage light">
  <div class="abs hero-welcome">Welcome to</div>
  <h1 class="abs hero-title">CHORDS BY LINDEN</h1>
  <div class="btn hero-btn">READ MORE</div>
</section>

<section class="about">
  <h2 class="abs section-title about-title"><span class="accent">ABOUT</span>CHORDS by Linden</h2>
  <div class="abs title-rule" style="top:101px"></div>
  <p class="abs lead about-lead">Lorem hendrerit in vulputate velit esse molestie consequat, velocity illum dolore eu feugiat nulla facilisis at vero eros et<br>accumsan etlict iusto odio dignissim qui blandit praesent luptatum zzril delenit loei augue duis dolore te feugait nulla facilisi.</p>
  <div class="abs about-photos">
    <div class="frame" style="left:7px;top:16px;width:270px;height:254px"></div>
    <div class="frame" style="left:95px;top:24px;width:227px;height:290px;background:#dcdcdc"></div>
    <div class="photo" role="img" aria-label="Photo of students playing piano and strings together" style="left:0;top:0;width:274px;height:244px;background:linear-gradient(135deg,#4a5a6a,#a27a5c 55%,#d8b89a)"></div>
    <div class="photo" role="img" aria-label="Photo of a grand piano in a bright studio room" style="left:152px;top:72px;width:274px;height:246px;background:linear-gradient(180deg,#ece8e0 0%,#d9d2c4 55%,#7a5a3a 100%)"></div>
  </div>
  <h3 class="abs about-heading">Playing the Piano</h3>
  <div class="abs about-copy">
    <p>When you think of a piano, you probably envision black and white keys but the piano is more than those harmonious sounds created by the player. The versatility and the musicianship instilled into the player from those keys is the true magic that comes from playing piano!</p>
    <p>Starting from the grassroots, experience different methods and styles of playing piano.</p>
  </div>
  <div class="btn about-btn">Read More</div>
</section>

<section class="vision" role="img" aria-label="Photo of piano keys in dark tones">
  <h2 class="abs section-title vision-title">OUR VISION</h2>
  <p class="abs lead vision-lead">Our Mission is Lorem ipsum dolor sit amet, consectetuer adipiscig elit, sed diama nonummy nibh euismod tincidunt<br>ut laoreet dolore magna aliquam erat volutpat. Ut wisi enim ad minim veniam. Lorem hendrerit in vulputate velit<br>esse molestie consequat, velocity illum dolore eu feugiat nulla facilisis at vero eros.</p>
  <div class="btn vision-btn">Contact Us Today</div>
</section>

<section class="programs">
  <h2 class="abs programs-title">Our programs also provide<br>students the opportunity to:</h2>
  <div class="abs programs-photo" role="img" aria-label="Photo of students practising on digital pianos in a classroom"></div>
  <div class="program-card" style="left:513px;top:146px"><p>Participate in large-scale performances.</p></div>
  <div class="program-card" style="left:791px;top:146px"><p>Perform at Linden's many community events on a regular basis.</p></div>
  <div class="program-card" style="left:513px;top:252px"><p>Access the GTA's coolest Broadcast stage</p></div>
  <div class="program-card" style="left:791px;top:252px"><p>Attend Clinics, Masterclasses, and Jam Nights</p></div>
  <div class="program-card" style="left:513px;top:358px"><p>Access the Linden Rocks band program. Linden's Band Program empowers.</p></div>
  <div class="program-card" style="left:791px;top:358px"><p>Register in our elite teaching program to learn how to pass on the magic.</p></div>
</section>

<section class="franchise">
  <h2 class="abs section-title franchise-title">Franchise Opportunities</h2>
  <p class="abs section-title franchise-sub">BE PART OF THE LINDEN CONSERVATORY FAMILY</p>
  <div class="btn franchise-btn">Know More</div>
</section>

<section class="quote">
  <div class="abs quote-accent"></div>
  <div class="abs quote-portrait" role="img" aria-label="Portrait photo of the quoted author"></div>
  <div class="abs quote-mark" style="left:484px;top:168px">&ldquo;</div>
  <p class="abs quote-text">Life is like a piano. What you get out of it depends on how you play it.</p>
  <div class="abs quote-mark" style="left:750px;top:224px">&rdquo;</div>
  <p class="abs quote-author">- THEO MARLOWE</p>
</section>

<section class="contact">
  <h2 class="abs section-title contact-title"><span class="accent">Contact</span> Us</h2>
  <div class="abs title-rule" style="top:120px"></div>
  <p class="abs lead contact-lead">Lorem Ipsum is Lorem ipsum dolor sit amet, consectetuer adipiscig elit, sed diama nonummy nibh euismod tincidunt<br>ut laoreet dolore magna aliquam erat volutpat. Ut wisi enim ad minim veniam.</p>
  <div class="abs contact-map" role="img" aria-label="Street map showing the studio location"></div>
  <form class="abs contact-form">
    <div class="field" style="top:30px">First Name</div>
    <div class="field" style="top:81px">Last Name</div>
    <div class="field" style="top:131px">What's Your Email?</div>
    <div class="field" style="top:183px;height:91px">Your Questions...</div>
    <div class="btn send-btn">SEND MESSGAE</div>
  </form>
</section>

<footer class="site-footer">
  <div class="info" style="left:183px;top:97px">
    <div class="info-icon"><svg width="24" height="32" viewBox="0 0 24 32"><path d="M12 0C5.4 0 0 5.4 0 12c0 9 12 20 12 20s12-11 12-20C24 5.4 18.6 0 12 0z" fill="#2b9ae8"/><circle cx="12" cy="12" r="4.5" fill="#fff"/></svg></div>
    <h3>Chords by Linden</h3>
    <p>123, Building Name, Street<br>City, State XY 123456</p>
  </div>
  <div class="info" style="left:476px;top:97px">
    <div class="info-icon"><svg width="28" height="28" viewBox="0 0 24 24"><path d="M6.6 10.8a15 15 0 0 0 6.6 6.6l2.2-2.2c.3-.3.7-.4 1-.2 1.1.4 2.3.6 3.6.6.6 0 1 .4 1 1V20c0 .6-.4 1-1 1A17 17 0 0 1 3 4c0-.6.4-1 1-1h3.5c.6 0 1 .4 1 1 0 1.3.2 2.5.6 3.6.1.3 0 .7-.2 1z" fill="#2b9ae8"/></svg></div>
    <h3>Call Us</h3>
    <p>1-888-555-0142</p>
  </div>
  <div class="info" style="left:758px;top:97px">
    <div class="info-icon"><svg width="30" height="22" viewBox="0 0 30 22"><rect width="30" height="22" rx="2" fill="#2b9ae8"/><path d="M1 2l14 11L29 2" fill="none" stroke="#fff" stroke-width="2"/></svg></div>
    <h3>Email Us</h3>
    <p>inquiry@chordsbylinden.example</p>
  </div>
  <div class="copyright">
    <p>Copyright © 2020 <strong>Chords By Linden</strong>. All Rights Reserved.</p>
    <div class="dots"><span></span><span></span><span></span><span></span></div>
  </div>
</footer>

</body>
</html>
```